Velk Partners Building Business Cards

We need a business card that reflects our business as "Solar Experts" in San Diego. Browse our website www.velkpartners.example our License needs to be displayed as "CSLB# 3867140" our phone number is (619) 555-0187

Save thousands on your electric bills and increase the value of your home while helping to protect the environment. Our solar installation experts will help you design the system that's right for you, using only the highest quality equipment that will look great and give you ideal performance. Our goal is to make you energy independent, and get your electric bill to 0.

Paul Osterby
(619) 555-0187
paul@velkpartners.example

Target Market(s)

Home owners in san diego looking for solar

Industry/Entity Type

Solar Energy

Contact Information for Business Card

Paul Osterby
(619) 555-0187
paul@velkpartners.example

Font styles to use
Other font styles liked:
• Use our logo font

Requirements
Must have
• License needs to be displayed as "CSLB# 3867140" our phone number is (619) 555-0187
Nice to have
• Real images of rooftop home solar in san diego
Should not have
• our business address

```html
<!DOCTYPE html>
<html lang="en">
<head>
<meta charset="utf-8">
<title>Velk Partners Building – Business Cards</title>
<link rel="stylesheet" href="https://fonts.googleapis.com/css2?family=Open+Sans:ital,wght@0,400;0,600;0,700;1,400&display=swap">
<style>
  :root {
    --navy: #183a73;
    --gold: #f2a600;
    --ink: #4a4a4a;
    --paper: #ffffff;
    --stage: #4f4f4f;
    --wash-warm: #fdf3dc;
    --wash-cool: #e6e9f1;
  }
  * { box-sizing: border-box; margin: 0; padding: 0; }
  html, body {
    width: 1105px;
    height: 1200px;
    overflow: hidden;
  }
  body {
    background: var(--stage);
    font-family: "Open Sans", Arial, sans-serif;
    position: relative;
  }
  .card {
    position: absolute;
    left: 193px;
    width: 719px;
    height: 410px;
    border-radius: 24px;
    overflow: hidden;
  }
  .card--front { top: 167px; background: var(--paper); }
  .card--back  { top: 623px; background: var(--navy); }

  .backdrop-art {
    position: absolute;
    right: 0;
    top: 40px;
    width: 430px;
    height: 370px;
    background: radial-gradient(ellipse at 70% 45%, var(--wash-warm) 0%, rgba(253,243,220,0.6) 45%, rgba(230,233,241,0.5) 70%, rgba(255,255,255,0) 90%);
  }

  .wordmark {
    position: absolute;
    font-weight: 700;
    white-space: nowrap;
    display: flex;
    align-items: center;
    gap: 12px;
  }
  .wordmark__dot {
    width: 16px;
    height: 16px;
    border-radius: 50%;
    background: var(--gold);
    flex: none;
  }
  .card--front .wordmark {
    left: 50px;
    top: 66px;
    font-size: 31px;
    color: var(--navy);
  }
  .card--back .wordmark {
    left: 0;
    right: 0;
    top: 170px;
    justify-content: center;
    font-size: 40px;
    color: var(--paper);
  }

  .license {
    position: absolute;
    left: 50px;
    top: 250px;
    font-size: 18px;
    color: var(--ink);
  }
  .contact-list {
    position: absolute;
    left: 50px;
    top: 287px;
    list-style: none;
    font-size: 18px;
    color: var(--ink);
    line-height: 27px;
  }
  .contact-list li { display: flex; align-items: center; gap: 9px; }
  .contact-list svg { width: 17px; height: 17px; fill: var(--navy); flex: none; }

  .person {
    position: absolute;
    right: 60px;
    top: 280px;
    text-align: right;
  }
  .person__name { font-size: 25px; font-weight: 600; color: var(--navy); line-height: 32px; }
  .person__role { font-size: 18px; color: var(--gold); line-height: 24px; }

  .back-url {
    position: absolute;
    left: 0;
    right: 0;
    top: 338px;
    text-align: center;
    font-size: 19px;
    font-style: italic;
    letter-spacing: 6px;
    color: var(--paper);
  }
</style>
</head>
<body>
  <section class="card card--front" aria-label="Card front">
    <div class="backdrop-art" role="img" aria-label="Faint decorative backdrop in warm and cool tints"></div>
    <div class="wordmark"><span class="wordmark__dot"></span>Velk Partners Building Inc</div>
    <p class="license">CSLB# 3867140</p>
    <ul class="contact-list">
      <li>
        <svg viewBox="0 0 24 24" aria-hidden="true"><path d="M6.6 10.8a15.1 15.1 0 0 0 6.6 6.6l2.2-2.2a1 1 0 0 1 1-.25 11.4 11.4 0 0 0 3.6.57 1 1 0 0 1 1 1V20a1 1 0 0 1-1 1A17 17 0 0 1 3 4a1 1 0 0 1 1-1h3.5a1 1 0 0 1 1 1c0 1.25.2 2.45.57 3.57a1 1 0 0 1-.25 1z"/></svg>
        (619) 555-0187
      </li>
      <li>
        <svg viewBox="0 0 24 24" aria-hidden="true"><path d="M2 5h20v14H2z M2 5l10 8 10-8" stroke="#fff" stroke-width="1.5"/></svg>
        paul@velkpartners.example
      </li>
      <li>
        <svg viewBox="0 0 24 24" aria-hidden="true"><circle cx="12" cy="12" r="10"/><path d="M2 12h20M12 2c3 3 3 17 0 20M12 2c-3 3-3 17 0 20" stroke="#fff" stroke-width="1.3" fill="none"/></svg>
        www.velkpartners.example
      </li>
    </ul>
    <div class="person">
      <p class="person__name">Paul Osterby</p>
      <p class="person__role">CEO/Founder</p>
    </div>
  </section>

  <section class="card card--back" aria-label="Card back">
    <div class="wordmark"><span class="wordmark__dot"></span>Velk Partners Building Inc</div>
    <p class="back-url">www.velkpartners.example</p>
  </section>
</body>
</html>
```